Vantiqo custom business card design

Need a authentic, innovative business card design for a new mobile app business. I am uploading a few screen images from our app for you to view. I would like app design theme to match business card design. I can also send logo images.

```html
<!DOCTYPE html>
<html lang="en">
<head>
<meta charset="utf-8">
<title>Vantiqo Business Card</title>
<link href="https://fonts.googleapis.com/css2?family=Montserrat:wght@400;700;800&family=Open+Sans:wght@400;600&display=swap" rel="stylesheet">
<style>
  :root {
    --bg: #e4e4e6;
    --card-white: #ffffff;
    --brand-purple: #5e0089;
    --ink: #1a1a1a;
    --on-purple: #ffffff;
    --on-purple-soft: rgba(255,255,255,0.85);
  }
  * { margin: 0; padding: 0; box-sizing: border-box; }
  html, body { width: 1200px; height: 900px; overflow: hidden; }
  body {
    background: var(--bg);
    display: flex;
    align-items: center;
    justify-content: center;
    gap: 48px;
    font-family: "Open Sans", Arial, sans-serif;
  }
  .card {
    width: 520px;
    height: 300px;
    border-radius: 26px;
    display: flex;
    flex-direction: column;
    align-items: center;
    box-shadow: 0 6px 18px rgba(0,0,0,0.12);
  }
  .card--front {
    background: var(--card-white);
    justify-content: center;
    padding-top: 6px;
  }
  .brand-mark {
    display: flex;
    flex-direction: column;
    align-items: center;
    gap: 10px;
  }
  .brand-mark__dot {
    width: 92px;
    height: 92px;
    border-radius: 50%;
    background: var(--brand-purple);
  }
  .brand-mark__name {
    font-family: "Montserrat", Arial, sans-serif;
    font-weight: 800;
    font-size: 40px;
    color: var(--ink);
    letter-spacing: 0.5px;
    line-height: 1;
  }
  .front-address {
    margin-top: 26px;
    font-family: "Montserrat", Arial, sans-serif;
    font-size: 13px;
    color: var(--ink);
    letter-spacing: 0.6px;
  }
  .card--back {
    background: var(--brand-purple);
    color: var(--on-purple);
    justify-content: center;
    text-align: center;
  }
  .back-brand {
    font-family: "Montserrat", Arial, sans-serif;
    font-weight: 800;
    font-size: 52px;
    line-height: 1;
    padding-bottom: 16px;
    border-bottom: 1px solid var(--on-purple-soft);
    width: 290px;
  }
  .person { margin-top: 14px; }
  .person__name {
    font-family: "Montserrat", Arial, sans-serif;
    font-weight: 700;
    font-size: 17px;
    letter-spacing: 0.5px;
  }
  .person__role {
    font-size: 12.5px;
    color: var(--on-purple-soft);
    margin-top: 2px;
  }
  .contact {
    margin-top: 14px;
    padding-top: 12px;
    border-top: 1px solid var(--on-purple-soft);
    width: 360px;
    font-size: 12.5px;
    line-height: 1.6;
  }
  .contact b { font-weight: 600; }
</style>
</head>
<body>
  <section class="card card--front">
    <div class="brand-mark">
      <span class="brand-mark__dot"></span>
      <span class="brand-mark__name">Vantiqo</span>
    </div>
    <p class="front-address">48 Harbor Lane, Eastbridge, Country Name, 10482.</p>
  </section>

  <section class="card card--back">
    <h1 class="back-brand">Vantiqo</h1>
    <div class="person">
      <p class="person__name">MARCUS HALE</p>
      <p class="person__role">Managing Director</p>
    </div>
    <div class="contact">
      <p><b>P:</b> 044-987 654 321 | <b>M:</b> 044-987 654 321</p>
      <p><b>E:</b> hello@vantiqo-app.com | <b>W:</b> www.vantiqo-app.com</p>
    </div>
  </section>
</body>
</html>
```